Boutique startup consulting

Hello,
Me and my partner are starting a boutique consulting/ "venturing for startup" firm and want to make professional looking slides. The point of these slide are to attract Automakers's venture arms to collaborate with us. We are hoping to win clients with this presentation.

Acceptance criteria:
1. You put beautiful designs where-ever you can and make the attached slides look professional. Full freedom in designing the slides. You are the artist, please create some magic
2. The style should be innovative and state of the art. It should be with colourful designs
3. The slides should be very professional
4. We are unsure of how to present our previous experience. Please help us out
5. The first slide has gray background. you may use the original colored image and tweak it

Here is out website:
https://www.talvora-partners.net/

Can you please ensure that the slides are presented in the following format?

PRESENTATION
1. Starting Masterslide
2. Customized Starting Masterslide (with Topic + Customer Logo, for eg. Smart City & KDR)
3. Service Categories Masterslide /Overview ( we have 5 Categories which are shown by icon and buzzword, see https://www.talvora-partners.net/live/research-strategy/research-strategy.aspx, this is for eg. the Overview for the categorie “Research &Strategy”. We have 2-4 Icon per Category, other categories are Business Development,Venture Building, Expansion Advisory, Sustainable Due Diligence , see webside)
4. Subcategories & Description Masterslide
o We have 15 Subcategories, the Masterslide should just show the Icon and then 1-2 square for description with bullets, f.ex. https://www.talvora-partners.net/live/expansion-advisory-feasibility-analysis/feasibility-analysis.aspx
5. Team Presenting Masterslide
o Not like Website, a Masterslide where each Teammember can present him self, in bullets with Education/Business Experience/ other awards/distinction AND in Text bubbles like “Experiences and hands-on Business developer”
6. Contact ( closing Chart with contact data, liked in etc.)
7. Masterslide (free for individual content)
o Just a slide with the CI framework which can be used as Masterslide for other charts like

8. PROPOSAL Masterslide (like customized starting slide, but Proposal)
9. Background Masterslide (Text)
o A textual description
10. Value Proposition & Goals Masterslide (Text & Bullets)
o V P will be textual so for eg. text frame; Goals with 2-4 squares (text/Bullets) for sub-goals and including the tasks for these goals in bullets
11. Milestones & Timing Masterslide (Timeline , Squares & text)
o Timeline, for eg. 6 Month project, where we have 8 tasks with starting and ending
12. Free MAsterslide /Proposal
o Where we can add charts to the proposal like Conditions or Contact

To Add:
- Logo colour description
- Picture and Icons ( so they don’t need to buy new pics or look for them)

Requirements
Must have
• Please check out the slides and make them presentable

```html
<!DOCTYPE html>
<html lang="en">
<head>
<meta charset="utf-8">
<title>Talvora Partners – Other Slides</title>
<link rel="stylesheet" href="https://fonts.googleapis.com/css2?family=Signika:wght@400;600;700&family=Fira+Sans:wght@400;500;700&display=swap">
<style>
:root{
  --stage:#4b4b4b;
  --ink-dark:#07160b;
  --green:#8dc63f;
  --green-bright:#a5c83a;
  --green-deep:#2f4f22;
  --panel-grey:#e6e6e6;
  --bar-dark:#3a3a3a;
  --band:#1d1d1d;
  --footer:#3c3c3c;
  --white:#ffffff;
  --text:#1e1e1e;
  --placeholder:#d4d4d4;
}
*{box-sizing:border-box;margin:0;padding:0}
html,body{width:1200px;height:693px;overflow:hidden;background:var(--stage)}
body{position:relative;font-family:"Fira Sans",sans-serif}
.slide{position:absolute;width:574px;height:323px;overflow:hidden}
.slide--cover{left:17px;top:12px;background:var(--ink-dark)}
.slide--mixed{left:609px;top:12px;background:var(--white)}
.slide--master{left:17px;top:353px;background:var(--green-bright)}
.slide--closing{left:609px;top:353px}
.abs{position:absolute}

/* brand wordmark */
.brand{position:absolute;display:flex;align-items:center;gap:5px;font-family:"Signika",sans-serif;font-weight:600;letter-spacing:.08em;text-transform:uppercase}
.brand__dot{width:12px;height:12px;border-radius:50%;background:var(--green)}

/* cover */
.cover__photo{left:0;top:0;width:574px;height:323px;background:linear-gradient(180deg,#0b2012 0%,#06130a 55%,#0a1d10 100%)}
.cover__mark{left:392px;top:30px;width:180px;height:290px;border-radius:90px 90px 40px 40px;background:radial-gradient(ellipse at 50% 35%,#9fd045 0%,#5f9b2c 45%,rgba(20,60,20,.0) 80%)}
.cover__rule{left:0;top:134px;width:213px;height:3px;background:var(--white)}
.cover__rule::before{content:"";position:absolute;left:0;top:0;width:54px;height:3px;background:var(--green)}
.cover__title{left:52px;top:149px;color:var(--white);font-family:"Signika",sans-serif;font-weight:600;font-size:21px;letter-spacing:.04em}

/* mixed content */
.mixed__panel{left:0;top:0;width:281px;height:302px;background:var(--panel-grey)}
.mixed__band{left:0;top:231px;width:281px;height:71px;background:var(--band);display:flex;align-items:center}
.kpi{display:flex;align-items:center;gap:7px;padding-left:20px;width:140px}
.kpi + .kpi{border-left:1px solid #555;padding-left:16px}
.kpi__value{font-family:"Signika",sans-serif;font-weight:700;color:var(--green);font-size:13px;line-height:1}
.kpi__note{color:#cfcfcf;font-size:4.5px;line-height:1.3;margin-top:2px}
.footer{position:absolute;left:0;top:302px;height:13px;display:flex;align-items:center;background:var(--footer);color:var(--white);font-size:6.6px;letter-spacing:.03em}
.footer__num{background:var(--green);height:13px;width:20px;display:flex;align-items:center;justify-content:center;font-weight:700;margin-right:6px}
.footer strong{font-weight:700}
.footer .hl{color:var(--green);font-weight:700}
.crumb{position:absolute;font-size:4.8px;letter-spacing:.05em;text-transform:uppercase;color:var(--green)}
.mixed__accent{left:321px;top:31px;width:53px;height:3px;background:var(--green)}
.mixed__head{left:321px;top:51px;width:220px;color:var(--green-bright);font-family:"Signika",sans-serif;font-weight:600;font-size:11.5px;line-height:1.25}
.col{position:absolute;font-size:6.6px;line-height:1.35;color:var(--text)}
.col p{margin-bottom:2px;text-align:justify}
.bullets{list-style:none}
.bullets li{position:relative;padding-left:10px;margin-bottom:4px}
.bullets li::before{content:"▷";position:absolute;left:0;top:0;color:var(--green)}

/* master */
.master__head{left:36px;top:26px;width:170px;color:var(--white);font-family:"Signika",sans-serif;font-weight:600;font-size:13.5px;line-height:1.3}
.master__rule{left:201px;top:33px;width:170px;height:3px;background:var(--white)}
.master__body{left:36px;top:79px;width:160px;font-size:8.7px;line-height:1.33;color:var(--text)}
.master__body p{margin-bottom:4px}
.master__body .bullets li::before{color:var(--white)}
.master__body .bullets li{margin-bottom:5px}
.placeholder{position:absolute;top:77px;width:164px;height:180px;background:var(--placeholder)}

/* closing */
.closing__photo{left:0;top:0;width:574px;height:323px;background:radial-gradient(ellipse at 55% 55%,#6f9a3e 0%,#3b6428 40%,#1d3a16 100%)}
.closing__title{left:39px;top:86px;color:var(--white);font-family:"Signika",sans-serif;font-weight:700;font-size:37px;line-height:1}
.closing__rule{left:39px;top:133px;width:60px;height:3px;background:var(--white)}
.contact{left:373px;top:0;width:161px;height:195px;background:var(--green-bright);color:var(--white);padding:38px 12px 0 20px}
.contact__city{font-family:"Signika",sans-serif;font-size:7.5px;letter-spacing:.25em;padding-bottom:4px;border-bottom:1px solid var(--white)}
.contact__name{font-family:"Signika",sans-serif;font-weight:600;font-size:7.5px;letter-spacing:.12em;margin:9px 0 12px}
.contact__lines{font-size:6.6px;line-height:1.9;padding-bottom:12px;border-bottom:1px solid var(--white)}
.contact__date{font-family:"Signika",sans-serif;font-weight:600;font-size:7.5px;letter-spacing:.12em;margin-top:8px}
.contact__brand{left:373px;top:195px;width:161px;height:52px;background:var(--white);display:flex;flex-direction:column;justify-content:center;padding-left:14px}
.contact__brand .brand{position:static;color:var(--green-deep);font-size:9.5px}
.contact__tag{font-size:4.5px;letter-spacing:.1em;color:#666;margin:2px 0 0 17px}
.closing__line{left:39px;top:269px;width:524px;height:1px;background:rgba(255,255,255,.8)}
.closing__topic{left:39px;top:276px;color:var(--white);font-family:"Signika",sans-serif}
.closing__topic b{display:block;font-size:12px;font-weight:600;letter-spacing:.03em}
.closing__topic span{display:block;font-size:10px;letter-spacing:.08em}
.partners{left:470px;top:278px;display:flex;align-items:center;gap:7px;color:var(--white);font-family:"Signika",sans-serif;font-weight:600;font-size:9px}
.partners__dot{width:14px;height:14px;border-radius:50%;background:var(--white)}
</style>
</head>
<body>

<!-- Section divider -->
<section class="slide slide--cover">
  <div class="abs cover__photo" role="img" aria-label="Dark night view of a city skyline"></div>
  <div class="abs cover__mark" role="img" aria-label="Large green brand emblem with skyline"></div>
  <div class="brand" style="left:52px;top:34px;color:var(--white);font-size:10px"><span class="brand__dot"></span>Talvora Partners</div>
  <div class="abs cover__rule"></div>
  <h1 class="abs cover__title">OTHER SLIDES</h1>
</section>

<!-- Mixed content -->
<section class="slide slide--mixed">
  <div class="abs mixed__panel"></div>
  <svg class="abs" style="left:34px;top:52px" width="90" height="175" viewBox="0 0 90 175" aria-label="Share infographics">
    <g font-family="Fira Sans,sans-serif" fill="#fff">
      <rect x="0" y="4" width="62" height="17" rx="4" fill="#3a3a3a"/>
      <rect x="0" y="21" width="62" height="17" rx="4" fill="#8dc63f"/>
      <text x="12" y="14" font-size="7" font-weight="700">50%</text><text x="12" y="19" font-size="3">Lorem ipsum</text>
      <text x="12" y="31" font-size="7" font-weight="700">50%</text><text x="12" y="36" font-size="3">Lorem ipsum</text>
      <circle cx="66" cy="21" r="20" fill="#fff"/>
      <circle cx="66" cy="21" r="17" fill="none" stroke="#8dc63f" stroke-width="5" stroke-dasharray="53 54"/>
      <circle cx="66" cy="21" r="17" fill="none" stroke="#3a3a3a" stroke-width="5" stroke-dasharray="0 53 54 0"/>
      <circle cx="66" cy="17" r="4" fill="none" stroke="#3a3a3a" stroke-width="1.2"/><path d="M59 29a7 6 0 0 1 14 0" fill="none" stroke="#3a3a3a" stroke-width="1.2"/>

      <rect x="0" y="66" width="62" height="11" rx="3" fill="#3a3a3a"/>
      <rect x="0" y="77" width="62" height="11" rx="3" fill="#8dc63f"/>
      <rect x="0" y="88" width="62" height="11" rx="3" fill="#b5b5b5"/>
      <text x="11" y="73" font-size="3">33% Lorem ipsum</text>
      <text x="11" y="84" font-size="3">33% Lorem ipsum</text>
      <text x="11" y="95" font-size="3">33% Lorem ipsum</text>
      <circle cx="66" cy="82" r="20" fill="#fff"/>
      <circle cx="66" cy="82" r="17" fill="none" stroke="#8dc63f" stroke-width="5"/>
      <circle cx="66" cy="82" r="17" fill="none" stroke="#3a3a3a" stroke-width="5" stroke-dasharray="36 71"/>
      <circle cx="66" cy="78" r="4" fill="none" stroke="#8dc63f" stroke-width="1.2"/><path d="M59 90a7 6 0 0 1 14 0" fill="none" stroke="#8dc63f" stroke-width="1.2"/>

      <rect x="0" y="128" width="62" height="10" rx="3" fill="#fff" stroke="#ccc" stroke-width=".5"/>
      <rect x="0" y="138" width="62" height="10" rx="3" fill="#b5b5b5"/>
      <rect x="0" y="148" width="62" height="10" rx="3" fill="#8dc63f"/>
      <rect x="0" y="158" width="62" height="10" rx="3" fill="#3a3a3a"/>
      <text x="11" y="134" font-size="3" fill="#333">25% Lorem ipsum</text>
      <text x="11" y="144" font-size="3">25% Lorem ipsum</text>
      <text x="11" y="154" font-size="3">25% Lorem ipsum</text>
      <text x="11" y="164" font-size="3">25% Lorem ipsum</text>
      <circle cx="66" cy="148" r="20" fill="#fff"/>
      <circle cx="66" cy="148" r="17" fill="none" stroke="#b5b5b5" stroke-width="5"/>
      <circle cx="66" cy="148" r="17" fill="none" stroke="#8dc63f" stroke-width="5" stroke-dasharray="27 80"/>
      <circle cx="66" cy="148" r="17" fill="none" stroke="#3a3a3a" stroke-width="5" stroke-dasharray="0 27 27 53"/>
      <circle cx="66" cy="144" r="4" fill="none" stroke="#8dc63f" stroke-width="1.2"/><path d="M59 156a7 6 0 0 1 14 0" fill="none" stroke="#8dc63f" stroke-width="1.2"/>
    </g>
  </svg>
  <svg class="abs" style="left:121px;top:56px" width="160" height="170" viewBox="0 0 160 170" aria-label="Monthly bar charts">
    <g font-family="Fira Sans,sans-serif" font-size="4.5" fill="#333">
      <line x1="16" y1="4" x2="16" y2="70" stroke="#333" stroke-width=".6"/>
      <line x1="16" y1="70" x2="150" y2="70" stroke="#333" stroke-width=".6"/>
      <text x="4" y="6">100</text><text x="7" y="22">75</text><text x="7" y="38">50</text><text x="7" y="54">25</text><text x="11" y="71">0</text>
      <g>
        <rect x="24" y="38" width="6" height="32" fill="#3a3a3a"/><rect x="24" y="16" width="6" height="22" fill="#8dc63f"/>
        <rect x="45" y="30" width="6" height="40" fill="#3a3a3a"/><rect x="45" y="7" width="6" height="23" fill="#8dc63f"/>
        <rect x="66" y="38" width="6" height="32" fill="#3a3a3a"/><rect x="66" y="10" width="6" height="28" fill="#8dc63f"/>
        <rect x="87" y="28" width="6" height="42" fill="#3a3a3a"/><rect x="87" y="8" width="6" height="20" fill="#8dc63f"/>
        <rect x="108" y="26" width="6" height="44" fill="#3a3a3a"/><rect x="108" y="12" width="6" height="14" fill="#8dc63f"/>
        <rect x="129" y="34" width="6" height="36" fill="#3a3a3a"/><rect x="129" y="20" width="6" height="14" fill="#8dc63f"/>
      </g>
      <text x="22" y="78">M1</text><text x="43" y="78">M2</text><text x="64" y="78">M3</text><text x="85" y="78">M4</text><text x="106" y="78">M5</text><text x="127" y="78">M6</text>

      <line x1="16" y1="92" x2="16" y2="160" stroke="#333" stroke-width=".6"/>
      <line x1="16" y1="160" x2="150" y2="160" stroke="#333" stroke-width=".6"/>
      <text x="4" y="94">100</text><text x="7" y="111">75</text><text x="7" y="128">50</text><text x="7" y="145">25</text><text x="11" y="161">0</text>
      <g>
        <rect x="24" y="128" width="6" height="32" fill="#8dc63f"/><rect x="24" y="102" width="6" height="26" fill="#3a3a3a"/><rect x="24" y="96" width="6" height="6" fill="#b5b5b5"/>
        <rect x="45" y="112" width="6" height="48" fill="#8dc63f"/><rect x="45" y="100" width="6" height="12" fill="#b5b5b5"/>
        <rect x="66" y="108" width="6" height="52" fill="#3a3a3a"/><rect x="66" y="98" width="6" height="10" fill="#8dc63f"/>
        <rect x="87" y="118" width="6" height="42" fill="#8dc63f"/><rect x="87" y="102" width="6" height="16" fill="#b5b5b5"/>
        <rect x="108" y="124" width="6" height="36" fill="#3a3a3a"/><rect x="108" y="100" width="6" height="24" fill="#8dc63f"/>
        <rect x="129" y="124" width="6" height="36" fill="#3a3a3a"/><rect x="129" y="108" width="6" height="16" fill="#8dc63f"/>
      </g>
      <text x="22" y="168">M1</text><text x="43" y="168">M2</text><text x="64" y="168">M3</text><text x="85" y="168">M4</text><text x="106" y="168">M5</text><text x="127" y="168">M6</text>
    </g>
  </svg>
  <div class="abs mixed__band">
    <div class="kpi">
      <svg width="20" height="14" viewBox="0 0 20 14"><polyline points="1,12 7,5 12,8 19,1" fill="none" stroke="#8dc63f" stroke-width="1.5"/><circle cx="1" cy="12" r="1.5" fill="#8dc63f"/><circle cx="7" cy="5" r="1.5" fill="#8dc63f"/><circle cx="12" cy="8" r="1.5" fill="#8dc63f"/><circle cx="19" cy="1" r="1.5" fill="#8dc63f"/></svg>
      <div><div class="kpi__value">233 PTS</div><div class="kpi__note">Lorem ipsum dolor sit amet,<br>consectetuer adipiscing elit.</div></div>
    </div>
    <div class="kpi">
      <svg width="16" height="16" viewBox="0 0 16 16"><path d="M14 2c-5 0-9 4-10 8l2 2c4-1 8-5 8-10z M4 10l-2 4 4-2" fill="none" stroke="#8dc63f" stroke-width="1.2"/></svg>
      <div><div class="kpi__value">25% MRR</div><div class="kpi__note">Lorem ipsum dolor sit amet,<br>consectetuer adipiscing elit.</div></div>
    </div>
  </div>
  <div class="footer" style="width:281px"><span class="footer__num">09</span>SMART MOBILITY &amp; KDR&nbsp;&gt;&gt;&nbsp;<strong>OTHER SLIDES</strong>&nbsp;&gt;&gt;&nbsp;<span class="hl">MIXED CONTENT</span></div>

  <div class="abs mixed__accent"></div>
  <div class="crumb" style="left:378px;top:31px">Other slides &gt;&gt; Mixed content &gt;&gt; Lorem ipsum dolor</div>
  <h2 class="abs mixed__head">Lorem ipsum dolor sit amet magna aliquam erat nibh.</h2>
  <div class="col" style="left:321px;top:111px;width:105px">
    <p>Consectetuer elit adipiscing, sed diam nonummy ex nibh. Euismod tincidunt ut laoreet dolore magna aliquam erat.</p>
    <p>Exerci ottatation ullamcorper suscipit lobortis ut nonummy aliquip exea commodo.</p>
    <ul class="bullets" style="margin-top:6px">
      <li>Lorem ipsum dolor sit amet laoreet aliquae ullamcorp</li>
      <li>Conseceur elit adisponti aed diam nonummy exea</li>
      <li>Euismod tincidunt ut laoreet dolore nisl adipisng</li>
      <li>Magna aliquam erat nibh ex ead commodo laoreet</li>
      <li>Exerci tation ullamcorper suscipit lobortis diam</li>
    </ul>
  </div>
  <div class="col" style="left:438px;top:98px;width:102px">
    <ul class="bullets">
      <li>Lorem ipsum dolor sit amet laoreet aliquae ullamcorp</li>
      <li>Conseceur elit adisponti aed am nonummy exea</li>
      <li>Euismod tincidunt ut laoreet dolore nisl adipisng</li>
      <li>Magna aliquam erat nibh ex ead commodo laoreet</li>
      <li>Exerci tation ullamcorper suscipit lobortis diam</li>
    </ul>
    <p>Consectetuer elit adipiscing, sed diam nonummy ex nibh. Euismod tincidunt ut laoreet dolore magna aliquam erat.</p>
    <p>Lorem ipsum dolor ullamcorper suscipit lobortis ut nonummy aliquip exea commodo.</p>
  </div>
  <div class="brand" style="left:472px;top:304px;color:var(--green-deep);font-size:6.5px"><span class="brand__dot" style="width:8px;height:8px"></span>Talvora Partners</div>
</section>

<!-- Free master -->
<section class="slide slide--master">
  <h2 class="abs master__head">Add the Slide Headline or Title Here_</h2>
  <div class="abs master__rule"></div>
  <div class="crumb" style="left:374px;top:32px;color:var(--white);font-weight:700">Other slides &gt;&gt; Green masterslide &gt;&gt; Lorem ipsum dolor</div>
  <div class="abs master__body">
    <p>Consectetuer elit adipiscing, sed dolorem diam nonummy ex nibh. Euismod tincidunt ut laoreet dolore magna aliquam erat.</p>
    <ul class="bullets">
      <li>Lorem ipsum dolor sit amet laoreet aliquae elit adipiscing</li>
      <li>Conseceur elit adisponti aed diam erat nonummy ex nibh</li>
      <li>Euismod tincidunt ut laoreet dolore nisl adipiscing sed</li>
      <li>Magna aliquam erat nibh ex commodo laoreet lorem</li>
      <li>Exerci tation ullamcorper suscipit lobortis diam</li>
    </ul>
  </div>
  <div class="placeholder" style="left:201px"></div>
  <div class="placeholder" style="left:380px"></div>
  <div class="footer" style="width:283px"><span class="footer__num" style="background:var(--white);color:var(--text)">12</span>SMART MOBILITY &amp; KDR&nbsp;&gt;&gt;&nbsp;<strong>OTHER SLIDES</strong>&nbsp;&gt;&gt;&nbsp;<span class="hl">GREEN MASTERSLIDE</span></div>
  <div class="brand" style="left:470px;top:305px;color:var(--white);font-size:6.5px"><span class="brand__dot" style="width:8px;height:8px;background:var(--white)"></span>Talvora Partners</div>
</section>

<!-- Closing -->
<section class="slide slide--closing">
  <div class="abs closing__photo" role="img" aria-label="Connected highway leading to a city skyline with network signals"></div>
  <h2 class="abs closing__title">Thank You</h2>
  <div class="abs closing__rule"></div>
  <div class="abs contact">
    <div class="contact__city">BERLIN</div>
    <div class="contact__name">MD LENNART VOSKAMP</div>
    <div class="contact__lines">
      E: voskamp@talvora.green<br>
      T: (+49) 151 0372 5580<br>
      W: talvora-partners.net<br>
      A: Lindenhof 14, D-10115
    </div>
    <div class="contact__date">NOV 2020</div>
  </div>
  <div class="abs contact__brand">
    <div class="brand"><span class="brand__dot"></span>Talvora Partners</div>
    <div class="contact__tag">Venture Consulting</div>
  </div>
  <div class="abs closing__line"></div>
  <div class="abs closing__topic"><b>SMART MOBILITY &amp; KDR</b><span>AN OVERVIEW</span></div>
  <div class="abs partners">
    <svg width="22" height="16" viewBox="0 0 22 16" aria-label="Connected car"><path d="M3 12V8l3-4h10l3 4v4z M3 12v2h3v-2 M16 12v2h3v-2" fill="none" stroke="#fff" stroke-width="1.2"/><circle cx="7" cy="9" r="1" fill="#fff"/><circle cx="15" cy="9" r="1" fill="#fff"/></svg>
    <span>+</span>
    <span class="partners__dot"></span><span>KDR</span>
  </div>
</section>

</body>
</html>
```